New Bottle Label for our Velinto Grand Reserva Brandy

Graphic Design Brief
We need a new bottle label for our Brandy Gran Reserva that we want to bring to the market.
Please have a look at all our current bottles and labels and the feel of our company under www.velinto-example.ch. We would like the design to be still different to the rest - as it is not a whisky, not a fruit product, not a spirit like a gin, thus we need to create like a new family, but still fitting in with the rest of the products.
The bottle that we will be using for the brand is a different one than the one that we already have, the design of the bottle is attached with a document.
I have also attached a briefing in regards to Brandy in general for your information.
### 1. What is Brandy?
Brandy is a distilled spirit made from fermented wine or other fruit wines. It is traditionally aged in oak barrels, which gives it its characteristic color and rich flavor. The aging process in oak is essential for developing the aromas and quality of the brandy.
### 2. What is Brandy Reserva?
A Brandy labeled as "Reserva" has undergone a longer aging process, typically at least 2 to 3 years, in oak barrels. This aging gives the brandy a deeper, more complex flavor profile and a darker color. "Reserva" is often an indication of higher quality.
### 3. Who enjoys drinking Brandy?
Brandy is typically favored by those who appreciate a deep, rich tasting experience. This often includes older consumers who value the time-aged complexity of the spirit. However, Brandy is also gaining popularity among younger people, especially through cocktails and modern serving styles.
### 4. Why is Brandy trending?
Brandy is experiencing a resurgence as consumers increasingly value quality and artisanal production methods. Its versatility in cocktails and association with traditional, luxurious experiences have also contributed to its renewed popularity.
### 5. What colors would be associated with Brandy?
The typical colors associated with Brandy are warm gold, amber, and deep golden-brown tones. These colors reflect the aging process in oak barrels and the richness of the flavors. Other associated colors might include dark brown and mahogany.
### 6. What is important to customers when buying Brandy?
Customers care about the origin of the Brandy, the aging time, the quality of the ingredients, the production method, and the brand. They also pay attention to the prestige of the product and the authenticity of the production.
### 7. What is not important to customers when buying Brandy?
For many customers, the price and packaging (unless it’s especially exclusive) may be less important than the quality and taste of the Brandy. The distillery name might be less significant if it isn’t tied to a particular reputation.
### 8. What do customers know about Swiss Brandy?
Swiss Brandy is still relatively unknown in many markets, but customers who are familiar with it appreciate the precision and quality of Swiss production. Swiss Brandy is assumed to be made with care and under strict quality standards.
### 9. What is Brandy Gran Reserva?
**Brandy Gran Reserva** is an even higher quality and longer-aged version of Brandy. Generally, a Gran Reserva is aged for at least 5 to 10 years or more in oak barrels. This extended aging process gives the Brandy an especially deep, complex flavor profile and often a darker, richer color. Gran Reserva is often regarded as the top-tier product within a Brandy range and appeals to discerning consumers who value quality, refinement, and a luxurious tasting experience.
The label “Gran Reserva” thus indicates the highest quality level for Brandies, similar to other spirits (like wine or whisky), where the aging time is a critical factor.
We age our Brandy Gran Reserva in the Solara way.
### 10. What emotions are associated with Brandy?
Brandy is often associated with luxury, relaxation, and comfort. It evokes feelings of tradition, elegance, and sophistication. Drinking Brandy is frequently seen as a moment of reflection and enjoyment.
### 11. How should Brandy be marketed?
Brandy should be marketed with a focus on its artisanal production, quality, and tradition. A narrative around the product, its aging, and origin can help create an emotional connection with the customer. The marketing should also emphasize the versatility of Brandy, whether consumed neat or in cocktails.
**Label design**:
The label should reflect the exclusivity of the product, with an elegant, minimalist design. The label should include information about the aging time, the use of oak barrels, and a brief story about the Brandy’s production.
we would like to have a modern look to the whole deisgn of the brandy
Target Market(s)
Customers that like Brandy
Target Market(s)
Switzerland
Industry/Entity Type
Distillery
Look and feel

```html
<!DOCTYPE html>
<html lang="en">
<head>
<meta charset="utf-8">
<title>Velinto Gran Reserva – Bottle Label</title>
<link rel="stylesheet" href="https://fonts.googleapis.com/css2?family=Marcellus&display=swap">
<style>
  :root {
    --backdrop: #faf7f2;
    --label-maroon: #560101;
    --label-gold: #e3bd66;
    --label-white: #ffffff;
  }
  html, body {
    margin: 0;
    padding: 0;
    overflow: hidden;
    background: var(--backdrop);
  }
  .canvas {
    position: relative;
    width: 1200px;
    height: 1200px;
    overflow: hidden;
    background: var(--backdrop);
    font-family: "Marcellus", serif;
  }
  .brand-name {
    position: absolute;
    left: 0;
    top: 38px;
    width: 100%;
    margin: 0;
    text-align: center;
    font-size: 104px;
    font-weight: 400;
    line-height: 1;
    letter-spacing: 0.02em;
    color: var(--label-maroon);
  }
  .label {
    position: absolute;
    left: 340px;
    top: 170px;
    width: 520px;
    height: 1000px;
    border-radius: 260px;
    background: var(--label-maroon);
  }
  .line {
    position: absolute;
    left: 0;
    width: 100%;
    margin: 0;
    text-align: center;
    line-height: 1;
    white-space: nowrap;
  }
  .brand-mark {
    position: absolute;
    left: 247px;
    top: 34px;
    width: 26px;
    height: 26px;
    background: var(--label-white);
    opacity: 0.9;
  }
  .category-small {
    font-size: 40px;
    letter-spacing: 0.12em;
    color: var(--label-white);
  }
  .category-swiss { top: 82px; }
  .category-premium { top: 138px; }
  .category-brandy {
    top: 194px;
    font-size: 62px;
    letter-spacing: 0.08em;
    color: var(--label-white);
  }
  .grade {
    font-size: 100px;
    color: var(--label-gold);
  }
  .grade-gran { top: 287px; }
  .grade-reserva { top: 407px; }
  .process {
    font-size: 36px;
    letter-spacing: 0.28em;
    color: var(--label-white);
  }
  .process-oak { top: 540px; }
  .process-solara { top: 596px; }
  .age-arc {
    position: absolute;
    left: 0;
    top: 650px;
    width: 520px;
    height: 280px;
  }
  .age-arc text {
    font-family: "Marcellus", serif;
    font-size: 30px;
    letter-spacing: 0.12em;
    fill: var(--label-white);
  }
  .age-number {
    top: 702px;
    font-size: 170px;
    color: var(--label-gold);
  }
  .divider {
    position: absolute;
    top: 732px;
    width: 3px;
    height: 102px;
    background: var(--label-white);
  }
  .divider-left { left: 158px; }
  .divider-right { left: 359px; }
  .spec {
    position: absolute;
    top: 750px;
    width: 120px;
    margin: 0;
    text-align: center;
    font-size: 26px;
    line-height: 1.25;
    letter-spacing: 0.3em;
    color: var(--label-white);
  }
  .spec-volume { left: 34px; }
  .spec-strength { left: 372px; }
</style>
</head>
<body>
<main class="canvas">
  <h1 class="brand-name">Velinto</h1>

  <section class="label" aria-label="Velinto Gran Reserva brandy label">
    <span class="brand-mark" aria-hidden="true"></span>

    <p class="line category-small category-swiss">SWISS</p>
    <p class="line category-small category-premium">PREMIUM</p>
    <p class="line category-brandy">BRANDY</p>

    <p class="line grade grade-gran">GRAN</p>
    <p class="line grade grade-reserva">RESERVA</p>

    <p class="line process process-oak">OAK BARREL</p>
    <p class="line process process-solara">SOLARA</p>

    <svg class="age-arc" viewBox="0 0 520 280" aria-hidden="true">
      <defs>
        <path id="arc-top" d="M165,135 A95,95 0 0 1 355,135"/>
        <path id="arc-bottom" d="M140,135 A120,120 0 0 0 380,135"/>
      </defs>
      <text><textPath href="#arc-top" startOffset="50%" text-anchor="middle">AGED</textPath></text>
      <text><textPath href="#arc-bottom" startOffset="50%" text-anchor="middle">YEARS</textPath></text>
    </svg>

    <p class="line age-number">5</p>

    <span class="divider divider-left" aria-hidden="true"></span>
    <span class="divider divider-right" aria-hidden="true"></span>

    <p class="spec spec-volume">50<br>CL</p>
    <p class="spec spec-strength">54%<br>VOL.</p>
  </section>
</main>
</body>
</html>
```